Business Card Design for a Personal Trainer

I need a business card design for my job as a personal trainer. It should have a unique, modern and exclusive design. On the front there should be only my logo with my name and my job. 0162/3819204 Tobias Lendhart Wiesengrundweg 14 80417 Munich Germany The most important contact information is the web adress. it can be bigger than the rest, but its not necessary. The card should be 8,5cmx5,5cm big. Font: Roboto. Colors: black, white, gray, 56c1ff.

```html
<!DOCTYPE html>
<html lang="de">
<head>
<meta charset="utf-8">
<title>Tobias Lendhart – Personal Trainer Business Card</title>
<link href="https://fonts.googleapis.com/css2?family=Roboto:wght@400;500&family=Old+Standard+TT:wght@700&display=swap" rel="stylesheet">
<style>
  :root {
    --cyan: #6de8fb;
    --white: #ffffff;
    --black: #141414;
    --gray: #8a8a8a;
    --stage: #e8e9ea;
  }
  * { box-sizing: border-box; margin: 0; padding: 0; }
  html, body { width: 1200px; height: 892px; overflow: hidden; }
  body {
    background: var(--stage);
    position: relative;
    font-family: "Roboto", Arial, sans-serif;
  }
  .card {
    position: absolute;
    top: 278px;
    width: 520px;
    height: 336px;
    box-shadow: 0 6px 18px rgba(0,0,0,0.18);
    overflow: hidden;
  }
  /* Back side */
  .card-back { left: 50px; background: var(--white); }
  .corner-accent {
    position: absolute;
    left: 0;
    width: 22px;
    height: 14px;
    background: var(--cyan);
  }
  .corner-accent.top { top: 0; }
  .corner-accent.bottom { bottom: 0; }
  .portrait {
    position: absolute;
    left: 58px;
    bottom: 0;
    width: 180px;
    height: 240px;
    background: linear-gradient(180deg, #e4e4e4 0%, #6a6a6a 45%, #2a2a2a 100%);
    border-radius: 70px 70px 0 0;
  }
  .back-brand {
    position: absolute;
    left: 260px;
    top: 58px;
    width: 220px;
    text-align: center;
    color: var(--cyan);
  }
  .brand-name {
    font-family: "Roboto", Arial, sans-serif;
    font-weight: 400;
    letter-spacing: 1px;
    white-space: nowrap;
  }
  .back-brand .brand-name { font-size: 21px; }
  .brand-role {
    display: flex;
    align-items: center;
    gap: 6px;
    font-size: 8.5px;
    letter-spacing: 3px;
    margin-top: 2px;
  }
  .brand-role::before, .brand-role::after {
    content: "";
    flex: 1;
    height: 1px;
    background: currentColor;
  }
  .contact-rule {
    position: absolute;
    left: 236px;
    top: 200px;
    width: 2px;
    height: 92px;
    background: var(--cyan);
  }
  .contact-list {
    position: absolute;
    left: 252px;
    top: 194px;
    list-style: none;
    font-family: "Old Standard TT", Georgia, serif;
    font-weight: 700;
    font-size: 14.5px;
    line-height: 17.5px;
    color: var(--black);
  }
  /* Front side */
  .card-front {
    left: 630px;
    background: var(--cyan);
    display: flex;
    align-items: center;
    justify-content: center;
  }
  .front-brand {
    color: var(--white);
    text-align: center;
  }
  .front-mark {
    width: 26px;
    height: 26px;
    margin: 0 auto 16px;
    background: var(--white);
  }
  .front-brand .brand-name { font-size: 30px; letter-spacing: 1.5px; }
  .front-brand .brand-role { font-size: 11px; letter-spacing: 4.5px; margin-top: 4px; }
</style>
</head>
<body>
  <section class="card card-back" aria-label="Business card back">
    <span class="corner-accent top"></span>
    <span class="corner-accent bottom"></span>
    <div class="portrait" role="img" aria-label="Black and white portrait of the trainer with arms crossed"></div>
    <div class="back-brand">
      <div class="brand-name">TOBIAS LENDHART</div>
      <div class="brand-role">PERSONAL TRAINER</div>
    </div>
    <span class="contact-rule"></span>
    <ul class="contact-list">
      <li>www.tobiaslendhart.de</li>
      <li>t.lendhart@mailbox.de</li>
      <li>0162/3819204</li>
      <li>Tobias Lendhart</li>
      <li>Wiesengrundweg 14</li>
      <li>80417 München</li>
    </ul>
  </section>

  <section class="card card-front" aria-label="Business card front">
    <div class="front-brand">
      <div class="front-mark"></div>
      <div class="brand-name">TOBIAS LENDHART</div>
      <div class="brand-role">PERSONAL TRAINER</div>
    </div>
  </section>
</body>
</html>
```